BOLD & MINIMALIST DESIGN NEEDED

We want a very bold but minimalistic business card design that is impactful and utilizes both sides of the business card. Our current logo is included for your use.

We want bold fonts and good use of negative space. We don't want the logo to overpower the design.

Target Market(s)

Professionals who are building new commercial buildings.

Industry/Entity Type

Construction

Contact Information for Business Card

Name, Title, email, office phone, cell phone, website

Font styles to use
Serif
Sans Serif

Requirements
Must have
• Bold design!

```html
<!DOCTYPE html>
<html lang="en">
<head>
<meta charset="utf-8">
<title>Ridgecrest Design + Build — Business Card</title>
<link rel="stylesheet" href="https://fonts.googleapis.com/css2?family=Poppins:wght@400;600;800&display=swap">
<style>
  :root {
    --bg: #1c1c1c;
    --card: #ffffff;
    --ink: #111111;
    --green: #7cc22a;
    --green-light: #9be330;
    --green-dark: #4f8d10;
    --rule: #9a9a9a;
  }
  * { box-sizing: border-box; margin: 0; padding: 0; }
  html, body { width: 1200px; height: 1108px; overflow: hidden; }
  body {
    background: var(--bg);
    font-family: "Poppins", sans-serif;
    position: relative;
  }
  .card {
    position: absolute;
    top: 204px;
    width: 400px;
    height: 700px;
    border-radius: 26px;
    overflow: hidden;
  }
  .card--front { left: 150px; background: var(--card); }
  .card--back { left: 650px; }

  .brand {
    position: absolute;
    top: 150px;
    left: 0;
    width: 100%;
    text-align: center;
  }
  .brand__mark {
    display: block;
    width: 46px;
    height: 46px;
    margin: 0 auto 18px;
    background: var(--green);
  }
  .brand__name {
    font-weight: 800;
    font-size: 44px;
    letter-spacing: 1px;
    line-height: 1;
    color: var(--ink);
    text-transform: uppercase;
  }
  .brand__tagline {
    font-weight: 800;
    font-size: 17px;
    letter-spacing: 6px;
    color: var(--ink);
    margin-top: 10px;
    text-transform: uppercase;
  }

  .person {
    position: absolute;
    top: 420px;
    width: 100%;
    text-align: center;
  }
  .person__name {
    font-weight: 800;
    font-size: 26px;
    color: var(--ink);
    text-transform: uppercase;
    letter-spacing: 0.5px;
  }
  .person__title {
    font-weight: 400;
    font-size: 15px;
    color: var(--green);
    text-transform: uppercase;
    letter-spacing: 1px;
    margin-top: 2px;
  }

  .icons {
    position: absolute;
    top: 500px;
    left: 40px;
    right: 40px;
    display: flex;
    align-items: center;
    gap: 8px;
  }
  .icons__rule { flex: 1; height: 1px; background: var(--rule); }
  .icons__tile {
    width: 30px; height: 30px;
    border-radius: 4px;
    background: var(--green);
    display: flex; align-items: center; justify-content: center;
  }
  .icons__tile svg { width: 18px; height: 18px; }

  .contact {
    position: absolute;
    top: 548px;
    width: 100%;
    text-align: center;
    list-style: none;
    font-size: 16px;
    line-height: 1.55;
    color: var(--ink);
  }
  .contact__accent { color: var(--green); }

  .pattern {
    position: absolute; inset: 0;
    background: linear-gradient(135deg, var(--green-light) 0%, var(--green) 50%, var(--green-dark) 100%);
  }
  .back-name {
    position: absolute;
    left: 0; right: 0;
    top: 480px;
    text-align: center;
    font-weight: 800;
    font-size: 16px;
    letter-spacing: 2px;
    color: var(--ink);
    text-transform: uppercase;
  }
</style>
</head>
<body>
  <section class="card card--front">
    <div class="brand">
      <span class="brand__mark"></span>
      <div class="brand__name">Ridgecrest</div>
      <div class="brand__tagline">Design + Build</div>
    </div>

    <div class="person">
      <div class="person__name">Marcus Hale</div>
      <div class="person__title">Managing Director</div>
    </div>

    <div class="icons">
      <span class="icons__rule"></span>
      <span class="icons__tile" title="Office phone">
        <svg viewBox="0 0 24 24" fill="#fff"><path d="M6.6 10.8a15 15 0 0 0 6.6 6.6l2.2-2.2c.3-.3.7-.4 1-.2 1.1.4 2.3.6 3.6.6.6 0 1 .4 1 1V20c0 .6-.4 1-1 1A17 17 0 0 1 3 4c0-.6.4-1 1-1h3.5c.6 0 1 .4 1 1 0 1.3.2 2.5.6 3.6.1.3 0 .7-.2 1z"/></svg>
      </span>
      <span class="icons__tile" title="Mobile">
        <svg viewBox="0 0 24 24" fill="none" stroke="#fff" stroke-width="2"><rect x="7" y="2.5" width="10" height="19" rx="2"/><line x1="11" y1="18" x2="13" y2="18"/></svg>
      </span>
      <span class="icons__tile" title="Email">
        <svg viewBox="0 0 24 24" fill="none" stroke="#fff" stroke-width="2"><rect x="3" y="5" width="18" height="14" rx="1"/><path d="M3 6l9 7 9-7"/></svg>
      </span>
      <span class="icons__tile" title="Website">
        <svg viewBox="0 0 24 24" fill="none" stroke="#fff" stroke-width="2"><circle cx="12" cy="12" r="9"/><path d="M3 12h18M12 3c3 3 3 15 0 18M12 3c-3 3-3 15 0 18"/></svg>
      </span>
      <span class="icons__rule"></span>
    </div>

    <ul class="contact">
      <li>021-555 0142</li>
      <li>021-555 0187</li>
      <li>hello@ridgecrestbuild.com</li>
      <li>www.<span class="contact__accent">ridgecrestbuild</span>.com</li>
    </ul>
  </section>

  <section class="card card--back">
    <div class="pattern" role="img" aria-label="Repeating tonal green pattern of the company monogram"></div>
    <div class="back-name">Ridgecrest</div>
  </section>
</body>
</html>
```